UPDATE 2: I HAVE ATTACHED TWO PHOTOS; PLEASE CONSIDER USING EITHER ONE IN A NEW DESIGN. THANK YOU.
UPDATE: I HAVE INCLUDED 4 SAMPLE BOOK COVERS THAT I LIKE TO HELP YOU ORIENT YOUR DESIGN WORK
Looking for book cover, spine, and back for a MEMOIR. Details:
TITLE: Mama's Quiet Orchard
AUTHOR: Lorisha Pemberfeld
GENRE: Memoir
STYLE REQUESTED: Abstract and colorful; designers are welcome to get creative. Note that the memoir takes place largely in a poor African American city.
BOOK SUMMARY: As a young girl, Lorisha Pemberfeld—or “Rishi” to her friends and family—discovers the man she thought was her father wasn’t, and her real biological father wants little if anything to do with her. What follows is the story of a girl’s longing, a longing disturbed by abuse, disappointment, and loneliness.
Set against the backdrop of Gary, Indiana—the then “murder capital of the world”—Mama’s Quiet Orchard follows Lorisha as she searches and grows, following a path that eventually leads her to self-discovery and self-confidence.
Template provided for InDesign. Please note margins and bleed areas. Make sure any letters/words are at least one inch from edges. On spine, leave three inches at bottom for publisher's logo.
Updates
To all designers: Please note that there should NOT be any images of people as part of your designs. Thank you, and my apologies for not mentioning that in the initial ask.

```html
<!DOCTYPE html>
<html lang="en">
<head>
<meta charset="utf-8">
<title>Mama’s Quiet Orchard — Book Cover</title>
<link rel="stylesheet" href="https://fonts.googleapis.com/css2?family=Anton&display=swap">
<style>
  :root {
    --ink-white: #ffffff;
    --shadow: rgba(40, 10, 20, 0.55);
    --red: #d9261c;
    --crimson: #b0182a;
    --orange: #f26a1b;
    --amber: #f4a21e;
    --green: #3fae3a;
    --blue: #1a6fc4;
    --deep-blue: #1d3f8f;
    --magenta: #c2206b;
  }
  * { margin: 0; padding: 0; box-sizing: border-box; }
  html, body { width: 779px; height: 1200px; overflow: hidden; background: var(--red); }
  .cover {
    position: relative;
    width: 779px;
    height: 1200px;
    overflow: hidden;
    font-family: "Anton", "Impact", sans-serif;
    font-weight: 400;
    color: var(--ink-white);
    text-align: center;
  }
  .cover-art {
    position: absolute;
    inset: 0;
    background:
      radial-gradient(ellipse 260px 200px at 30% 48%, rgba(90, 180, 60, 0.85), transparent 70%),
      radial-gradient(ellipse 220px 180px at 60% 58%, rgba(240, 190, 40, 0.7), transparent 70%),
      radial-gradient(ellipse 300px 160px at 60% 76%, rgba(26, 111, 196, 0.8), transparent 70%),
      radial-gradient(ellipse 200px 200px at 12% 72%, rgba(242, 106, 27, 0.8), transparent 70%),
      radial-gradient(ellipse 240px 160px at 85% 10%, rgba(30, 100, 200, 0.7), transparent 70%),
      radial-gradient(ellipse 260px 200px at 18% 8%, rgba(242, 120, 30, 0.85), transparent 70%),
      linear-gradient(180deg, var(--crimson) 0%, var(--red) 35%, var(--orange) 60%, var(--magenta) 85%, var(--deep-blue) 100%);
  }
  .title, .tagline, .author { margin: 0; font-weight: 400; }
  .title-line, .tagline, .author-line {
    position: absolute;
    left: 0;
    right: 0;
    display: block;
    line-height: 1;
    white-space: nowrap;
    text-transform: uppercase;
    text-shadow: 3px 4px 6px var(--shadow);
  }
  .title-line { font-size: 162px; }
  .title-line--1 { top: 105px; }
  .title-line--2 { top: 254px; }
  .title-line--3 { top: 403px; }
  .tagline {
    top: 663px;
    font-size: 52px;
    letter-spacing: 8px;
  }
  .author-line--first { top: 802px; font-size: 130px; }
  .author-line--last { top: 944px; font-size: 124px; }
</style>
</head>
<body>
  <main class="cover">
    <div class="cover-art" role="img" aria-label="Abstract painted collage in red, orange, green and blue with a flock of dark birds in flight"></div>
    <h1 class="title">
      <span class="title-line title-line--1">Mama’s</span>
      <span class="title-line title-line--2">Quiet</span>
      <span class="title-line title-line--3">Orchard</span>
    </h1>
    <p class="tagline">A Memoir</p>
    <p class="author">
      <span class="author-line author-line--first">Lorisha</span>
      <span class="author-line author-line--last">Pemberfeld</span>
    </p>
  </main>
</body>
</html>
```